Business card design

I need my logo on this card, things I need the card to have on it
licensed and insured.
owner operators Milo & Trent Halvorsen
my phone number 5083716254
Disaster Recovery, Storm Damage Restoration, Proactive Disaster Plan Management, Roof Repair/Restoration Structural Repair and Reconstruction, Emergency Boarding and Tarping Service, Perimeter Fencing, Emergency Tree Removal,

```html
<!DOCTYPE html>
<html lang="en">
<head>
<meta charset="utf-8">
<title>Halvorsen's Construction L.L.C — Business Card</title>
<link href="https://fonts.googleapis.com/css2?family=Nunito:wght@400;500&display=swap" rel="stylesheet">
<style>
  :root {
    --backdrop: #a3a3a3;
    --card-dark: #111111;
    --card-light: #ffffff;
    --brand-blue: #3a8fd0;
    --ink-dark: #1b1b1b;
    --ink-light: #f2f2f2;
    --rule-grey: #7a7b7f;
  }
  * { margin: 0; padding: 0; box-sizing: border-box; }
  html, body { width: 1093px; height: 1200px; overflow: hidden; }
  body {
    background: var(--backdrop);
    font-family: "Nunito", sans-serif;
    position: relative;
  }
  .card {
    position: absolute;
    border-radius: 18px;
    overflow: hidden;
    box-shadow: 0 2px 6px rgba(0,0,0,0.25);
  }
  .card--front { left: 265px; top: 224px; width: 580px; height: 362px; background: var(--card-dark); }
  .card--back  { left: 261px; top: 619px; width: 596px; height: 363px; background: var(--card-light); }

  .brand {
    position: absolute;
    width: 220px;
    text-align: center;
  }
  .brand__mark {
    display: block;
    width: 34px; height: 34px;
    margin: 0 auto 16px;
    background: var(--brand-blue);
  }
  .brand__name {
    color: var(--brand-blue);
    font-size: 22px;
    font-weight: 500;
    line-height: 1.25;
  }
  .card--front .brand { left: 40px; top: 110px; }
  .card--back  .brand { left: 47px; top: 108px; }

  .divider { position: absolute; width: 1.5px; }
  .card--front .divider { left: 272px; top: 91px; height: 179px; background: var(--brand-blue); }
  .card--back  .divider { left: 293px; top: 83px; height: 190px; background: var(--rule-grey); }

  .services {
    position: absolute;
    left: 282px; top: 86px;
    width: 285px;
    list-style: none;
    color: var(--ink-light);
    font-size: 14px;
    line-height: 19px;
  }
  .services li { position: relative; padding-left: 12px; margin-bottom: 6.3px; }
  .services li::before {
    content: "";
    position: absolute; left: 0; top: 6px;
    width: 7px; height: 7px; border-radius: 50%;
    background: var(--brand-blue);
  }

  .contact { position: absolute; left: 304px; top: 78px; color: var(--ink-dark); }
  .contact__names { color: var(--brand-blue); font-size: 22px; font-weight: 500; line-height: 1.2; }
  .contact__role { font-size: 13.5px; margin-top: 2px; line-height: 17px; }
  .contact__address { font-size: 13.5px; line-height: 16px; margin-top: 12px; }
  .contact__lines { list-style: none; margin-top: 10px; font-size: 13.5px; }
  .contact__lines li { display: flex; align-items: center; height: 23.5px; }
  .contact__lines svg { width: 15px; height: 14px; margin-right: 9px; flex: none; }
  .contact__lines .phone span { margin-left: 6px; letter-spacing: 0.5px; }

  .band-rule { position: absolute; left: 0; top: 320px; width: 100%; height: 4px; background: var(--rule-grey); }
  .band { position: absolute; left: 0; top: 326px; width: 100%; height: 37px; background: var(--brand-blue); }
</style>
</head>
<body>

<section class="card card--front">
  <div class="brand">
    <span class="brand__mark"></span>
    <p class="brand__name">Halvorsen's<br>Construction L.L.C</p>
  </div>
  <div class="divider"></div>
  <ul class="services">
    <li>Disaster Recovery</li>
    <li>Storm Damage Restoration</li>
    <li>Proactive Disaster Plan Management</li>
    <li>Perimeter Fencing</li>
    <li>Emergency Boarding and Tarping Service</li>
    <li>Emergency Tree Removal</li>
    <li>Roof Repair/Restoration Structural Repair And Reconstruction</li>
  </ul>
</section>

<section class="card card--back">
  <div class="brand">
    <span class="brand__mark"></span>
    <p class="brand__name">Halvorsen's<br>Construction L.L.C</p>
  </div>
  <div class="divider"></div>
  <div class="contact">
    <p class="contact__names">Milo &amp; Trent Halvorsen</p>
    <p class="contact__role">owner operators</p>
    <p class="contact__role">licensed and insured</p>
    <p class="contact__address">48 Cedar Hollow Road<br>Brandon, MS 39042</p>
    <ul class="contact__lines">
      <li class="phone">
        <svg viewBox="0 0 16 14" aria-hidden="true"><path d="M1 5c0-2 3-3 7-3s7 1 7 3v1h-3V4.5C10.5 4 9 4 8 4s-2.5 0-4 .5V6H1z" fill="#3a8fd0"/><path d="M4 7h8l1.5 6h-11z" fill="#3a8fd0"/><circle cx="8" cy="10" r="1.6" fill="#fff"/></svg>
        <span>5083716254</span>
      </li>
      <li>
        <svg viewBox="0 0 16 14" aria-hidden="true"><rect x="0.5" y="2" width="15" height="11" rx="1" fill="#3a8fd0"/><path d="M1 3l7 5.5L15 3" fill="none" stroke="#fff" stroke-width="1.3"/></svg>
        info@halvorsenbuild.com
      </li>
      <li>
        <svg viewBox="0 0 16 16" aria-hidden="true"><circle cx="8" cy="8" r="7" fill="#3a8fd0"/><path d="M1 8h14M8 1c-3 3-3 11 0 14M8 1c3 3 3 11 0 14" fill="none" stroke="#fff" stroke-width="1.1"/></svg>
        www.halvorsenbuild.com
      </li>
    </ul>
  </div>
  <div class="band-rule"></div>
  <div class="band"></div>
</section>

</body>
</html>
```